Web design project for exciting Australian start-up

Background
We are looking for a creative and talented web design artist to work alongside our market leading web developer.
• You will be required to create a modern and clean design theme for our website, incorporating selected rustic colour scheme elements for our exciting Australian start-up to operate within the coffee industry.
reoccurring work to be expected to flow to the successful designer.
Requirements
• c. 5 - 10 page website
• Landing page
• Log in/ out
• 404 template
• Typography is emphasised
• Please use either a) typemarrow.com, b) free web fonts, c) brindle fonts
• All design elements in vector format
• Preferably with icons for each header title(i.e. about us, how it works etc) but designer have free reign over how the site looks, so might not be applicable
• All pages to be responsive
• Down to eSlab resolution

High level visual design brief attached - additional pages to be worked from base design.

Design inspiration
• We would like to use design elements from the following sources:
http://www.zandrix.com/halcyon/ (Functionality)
Colour scheme refer to logo and complementary style guide

```html
<!DOCTYPE html>
<html lang="en">
<head>
<meta charset="utf-8">
<title>Roastwell Hub – Select</title>
<link rel="stylesheet" href="https://fonts.googleapis.com/css2?family=Varela+Round&family=Roboto+Slab:wght@400;700&family=Open+Sans:wght@700&display=swap">
<style>
  :root {
    --red: #e8393c;
    --orange: #ffa033;
    --dark: #444445;
    --mid-grey: #707071;
    --white: #ffffff;
    --ink: #1a1a1a;
    --text: #4a4a4a;
    --footer-bg: #e8e8e8;
    --bar-bg: #575757;
    --rule: #e4e4e4;
  }
  * { box-sizing: border-box; margin: 0; padding: 0; }
  html, body { width: 1200px; height: 950px; overflow: hidden; }
  body { position: relative; font-family: "Varela Round", sans-serif; background: var(--white); color: var(--text); }
  .abs { position: absolute; }

  /* header */
  .site-header { position: absolute; left: 0; top: 0; width: 1200px; height: 107px; background: var(--white); }
  .brand { left: 161px; top: 34px; display: flex; align-items: center; gap: 10px; }
  .brand-mark { width: 40px; height: 40px; border-radius: 50%; background: var(--orange); }
  .brand-name { font-family: "Roboto Slab", serif; font-weight: 700; font-size: 22px; letter-spacing: 1px; color: var(--ink); text-transform: uppercase; }
  .nav-item { top: 0; height: 107px; border-left: 1px solid var(--rule); display: flex; flex-direction: column; align-items: center; justify-content: center; gap: 6px; font-size: 11.5px; color: #333; text-transform: uppercase; }
  .nav-item.last { border-right: 1px solid var(--rule); }
  .nav-item svg { width: 20px; height: 20px; }
  .btn { top: 38px; height: 31px; display: flex; align-items: center; justify-content: center; color: var(--white); font-size: 14px; border-radius: 2px; }
  .btn-red { background: var(--red); }
  .btn-orange { background: var(--orange); }

  /* hero */
  .hero { left: 0; top: 107px; width: 1200px; height: 543px;
    background: radial-gradient(ellipse 40% 55% at 45% 35%, #7a3f1c 0%, #3a1a0b 45%, #0c0604 80%),
                #0c0604; }
  .hero::after { content: ""; position: absolute; left: 260px; right: 140px; bottom: 0; height: 80px;
    background: radial-gradient(ellipse 55% 100% at 50% 100%, #6b4020 0%, #2a160a 60%, transparent 100%); }

  .select-panel { left: 272px; top: 152px; width: 655px; height: 452px; background: var(--white); }
  .close { left: 902px; top: 140px; width: 38px; height: 38px; border-radius: 50%; background: var(--red); color: var(--white); font-family: "Open Sans", sans-serif; font-weight: 700; font-size: 17px; display: flex; align-items: center; justify-content: center; }
  .panel-title { left: 312px; top: 183px; font-family: "Roboto Slab", serif; font-weight: 700; font-size: 17px; color: var(--ink); }

  .opt { left: 313px; width: 184px; height: 38px; padding: 0 20px; display: flex; align-items: center; justify-content: space-between; color: var(--white); font-size: 14.5px; background: var(--orange); }
  .opt.active { background: var(--red); }
  .opt svg { width: 6px; height: 9px; }

  .submenu { width: 184px; background: var(--dark); color: var(--white); font-size: 14.5px; }
  .submenu::before { content: ""; position: absolute; left: -7px; top: 17px; border: 7px solid transparent; border-left: 0; border-right-color: var(--dark); }
  .submenu .row { height: 43px; padding-left: 28px; display: flex; align-items: center; border-bottom: 1px solid #5d5d5e; }
  .submenu .row:last-child { border-bottom: 0; }
  .submenu .row.on { background: var(--mid-grey); }

  .launch { left: 701px; top: 520px; width: 184px; height: 50px; background: var(--red); color: var(--white); font-family: "Open Sans", sans-serif; font-weight: 700; font-size: 15px; display: flex; align-items: center; justify-content: center; gap: 8px; }
  .launch svg { width: 8px; height: 12px; }

  /* footer */
  .site-footer { left: 0; top: 650px; width: 1200px; height: 236px; background: var(--footer-bg); }
  .footer-col { top: 700px; }
  .footer-col h3 { font-family: "Roboto Slab", serif; font-weight: 400; font-size: 17.5px; color: var(--ink); text-transform: uppercase; margin-bottom: 18px; }
  .footer-col li { list-style: none; font-size: 14px; color: var(--text); height: 31px; display: flex; align-items: center; gap: 15px; }
  .social-dot { width: 11px; height: 11px; background: var(--text); border-radius: 2px; }
  .bottom-bar { left: 0; top: 886px; width: 1200px; height: 64px; background: var(--bar-bg); }
  .bottom-bar::before { content: ""; position: absolute; left: 161px; right: 161px; top: 6px; border-top: 1px solid #6a6a6a; }
  .copyright { width: 100%; top: 906px; text-align: center; color: var(--white); font-size: 14px; }
</style>
</head>
<body>

<header class="site-header">
  <div class="abs brand">
    <span class="brand-mark"></span>
    <span class="brand-name">Roastwell Hub</span>
  </div>

  <nav>
    <a class="abs nav-item" style="left:423px;width:94px;">
      <svg viewBox="0 0 20 20" fill="none" stroke="#ffa033" stroke-width="1.4"><path d="M3 10 L10 3 L17 10"/><path d="M5 9 V17 H15 V9"/><path d="M8.5 17 V12 H11.5 V17"/></svg>
      About us
    </a>
    <a class="abs nav-item" style="left:517px;width:136px;">
      <svg viewBox="0 0 20 20" fill="none" stroke="#666" stroke-width="1.3"><circle cx="8" cy="7" r="3"/><path d="M2 17 C2 12 14 12 14 17"/><rect x="12" y="2" width="6" height="5"/></svg>
      How it works
    </a>
    <a class="abs nav-item last" style="left:653px;width:65px;">
      <svg viewBox="0 0 20 20" fill="none" stroke="#666" stroke-width="1.3"><rect x="4" y="5" width="4" height="13"/><rect x="11" y="2" width="4" height="16"/></svg>
      FAQ
    </a>
  </nav>

  <a class="abs btn btn-red" style="left:750px;width:119px;">My Account</a>
  <a class="abs btn btn-orange" style="left:878px;width:76px;">Login</a>
  <a class="abs btn btn-red" style="left:963px;width:76px;">Sign up</a>
</header>

<section class="abs hero" role="img" aria-label="Warm dark photograph of roasted coffee beans"></section>

<div class="abs select-panel"></div>
<div class="abs close">x</div>
<h2 class="abs panel-title">SELECT</h2>

<div class="abs opt active" style="top:224px;">Tender type <svg viewBox="0 0 6 9"><path d="M0 0 L6 4.5 L0 9Z" fill="#fff"/></svg></div>
<div class="abs opt" style="top:271px;">Quantity (kg) <svg viewBox="0 0 6 9"><path d="M0 0 L6 4.5 L0 9Z" fill="#fff"/></svg></div>
<div class="abs opt" style="top:318px;">Wholesaler <svg viewBox="0 0 6 9"><path d="M0 0 L6 4.5 L0 9Z" fill="#fff"/></svg></div>
<div class="abs opt" style="top:390px;">Machinery <svg viewBox="0 0 6 9"><path d="M0 0 L6 4.5 L0 9Z" fill="#fff"/></svg></div>
<div class="abs opt" style="top:437px;">Barista training <svg viewBox="0 0 6 9"><path d="M0 0 L6 4.5 L0 9Z" fill="#fff"/></svg></div>
<div class="abs opt" style="top:484px;">Accessories <svg viewBox="0 0 6 9"><path d="M0 0 L6 4.5 L0 9Z" fill="#fff"/></svg></div>
<div class="abs opt" style="top:531px;">Promotion support <svg viewBox="0 0 6 9"><path d="M0 0 L6 4.5 L0 9Z" fill="#fff"/></svg></div>

<div class="abs submenu" style="left:509px;top:224px;">
  <div class="row">One-off</div>
  <div class="row on">Recurring</div>
</div>
<div class="abs submenu" style="left:701px;top:267px;">
  <div class="row">6 months</div>
  <div class="row">12 months</div>
</div>

<a class="abs launch">LAUNCH SEARCH <svg viewBox="0 0 8 12" fill="none" stroke="#fff" stroke-width="2"><path d="M1 1 L6 6 L1 11"/></svg></a>

<footer>
  <div class="abs site-footer"></div>
  <div class="abs footer-col" style="left:295px;">
    <h3>Helpful Info</h3>
    <ul><li>About Us</li><li>Media Enquiries</li><li>Terms &amp; Conditions</li><li>Privacy Policy</li></ul>
  </div>
  <div class="abs footer-col" style="left:541px;">
    <h3>Who We Are</h3>
    <ul style="padding-left:8px;"><li>How it works</li><li>FAQ</li><li>Contact us</li></ul>
  </div>
  <div class="abs footer-col" style="left:798px;">
    <h3>Join Us On</h3>
    <ul style="padding-left:3px;">
      <li>Chatterbook <span class="social-dot"></span></li>
      <li>Chirpline <span class="social-dot"></span></li>
      <li>Linkworks <span class="social-dot"></span></li>
      <li>Clipstream <span class="social-dot"></span></li>
    </ul>
  </div>
  <div class="abs bottom-bar"></div>
  <p class="abs copyright">Copyright © 2014 Roastwell Hub</p>
</footer>

</body>
</html>
```